Varentoria Business Card and Letter Head

We are a leadership assessment consultancy based in Sydney, Australia. We help executive-level decison-makers select leaders for more senior level roles in corporate and government organisations. Our methodology is based on the latest research from the field of neuroscience.
We need a business card design and matching letter head that presents our company, Varentoria, as a:
1. trusted adviser to senior executive-level decison makers
2. niche consultancy who are experts in the field of assessing leadership talent
3. results-focused solution provider who balance scientific methods with pragmatic solutions
The following company details should be used in all designs:
Company Name: Varentoria
Details (for business card):
Derek Hanford
Prime Capacity Officer
Level 17, Marlow Tower
7 Marlow Square
Sydney, NSW 2011 Australia
Phone: 1300 582 714
Mobile: 0412 637 258
Email: derek.hanford@varentoria-example.com.au
Website: varentoria-example.com.au
I have attached the logo for Varentoria (for both a white and black background) - your business card and letter head designs must incoporate this logo and colour scheme.
Thanks for your interest in this project, I'm looking forward to receiving your ideas.
Regards,
Derek
Target Market(s)
Executive-level decison-makers in corporate and government organisations (e.g., CEO, VP, Head of Human Resources)
Industry/Entity Type
Leadership
Look and feel

```html
<!DOCTYPE html>
<html lang="en">
<head>
<meta charset="utf-8">
<title>Varentoria Business Card</title>
<link rel="stylesheet" href="https://fonts.googleapis.com/css2?family=Source+Sans+3:wght@400;600;700&display=swap">
<style>
  :root {
    --backdrop: #ebe7e1;
    --card: #ffffff;
    --ink: #3d3d3d;
    --ink-soft: #5a5a5a;
    --rule: #6b6b6b;
    --accent: #b8322a;
  }
  * { margin: 0; padding: 0; box-sizing: border-box; }
  html, body {
    width: 1200px; height: 469px; overflow: hidden;
    background: var(--backdrop);
    font-family: "Source Sans 3", "Myriad Pro", sans-serif;
    color: var(--ink);
  }
  .stage { position: relative; width: 1200px; height: 469px; }
  .card {
    position: absolute; top: 85px; width: 526px; height: 296px;
    background: var(--card);
    box-shadow: 0 2px 6px rgba(0,0,0,0.18);
  }
  .card--front { left: 47px; }
  .card--back { left: 620px; }

  .brand { position: absolute; left: 46px; top: 66px; display: flex; align-items: center; gap: 14px; }
  .brand__mark { width: 60px; height: 60px; background: var(--ink); }
  .brand__text { display: flex; flex-direction: column; }
  .brand__name { font-size: 40px; font-weight: 700; line-height: 1; letter-spacing: -0.5px; color: var(--ink); }
  .brand__tagline { font-size: 11.5px; font-weight: 400; letter-spacing: 0.3px; color: var(--ink-soft); margin-top: 6px; text-transform: uppercase; }

  .divider { position: absolute; left: 0; right: 0; top: 149px; height: 18px; display: flex; align-items: center; }
  .divider__rule { height: 2px; background: var(--rule); flex: 1; }
  .divider__rule--end { flex: 0 0 50px; }
  .divider__label { padding: 0 13px; line-height: 18px; }

  .card--front .divider { right: 28px; }
  .card--front .divider__rule--end { flex: 0 0 18px; }
  .card--front .divider__label { padding: 0 12px 0 15px; }

  .person__name { font-size: 16px; font-weight: 700; color: var(--accent); }
  .person__role { position: absolute; top: 166px; right: 58px; font-size: 11.5px; color: var(--ink); line-height: 1.3; }

  .contacts { position: absolute; right: 58px; top: 188px; list-style: none; }
  .contacts li { display: flex; justify-content: flex-end; align-items: center; gap: 9px; font-size: 11.5px; color: var(--ink-soft); height: 17px; }
  .contacts svg { width: 11px; height: 11px; fill: var(--accent); flex: none; }

  .address { position: absolute; left: 118px; top: 262px; font-size: 11.5px; color: var(--ink-soft); }

  .web { font-size: 13px; color: var(--ink); }
  .web__accent { color: var(--accent); }
</style>
</head>
<body>
<main class="stage">
  <section class="card card--front" aria-label="Business card front">
    <div class="brand">
      <div class="brand__mark"></div>
      <div class="brand__text">
        <span class="brand__name">Varentoria</span>
        <span class="brand__tagline">Assessing Executive Potential</span>
      </div>
    </div>

    <div class="divider">
      <span class="divider__rule"></span>
      <span class="divider__label person__name">Derek Hanford</span>
      <span class="divider__rule divider__rule--end"></span>
    </div>
    <div class="person__role">Prime Capacity Officer</div>

    <ul class="contacts">
      <li>1300 582 714
        <svg viewBox="0 0 12 12"><path d="M2.5 1l2 2.2-1 1.3c.7 1.5 1.8 2.6 3.3 3.3l1.3-1L10.5 8.6 9.3 10.8C5 10.5 1.5 7 1.2 2.7z"/></svg></li>
      <li>0412 637 258
        <svg viewBox="0 0 12 12"><path d="M3.5 0h5v12h-5zM4.5 1.5v6h3v-6z"/></svg></li>
      <li>derek.hanford@varentoria-example.com.au
        <svg viewBox="0 0 12 12"><path d="M0 2.5h12v7H0zM1 3.3l5 3.4 5-3.4z" fill-rule="evenodd"/></svg></li>
      <li>www.varentoria-example.com.au
        <svg viewBox="0 0 12 12"><circle cx="6" cy="6" r="5.5"/><path d="M0.5 6h11M6 0.5v11" stroke="#fff" stroke-width="0.8"/></svg></li>
    </ul>

    <p class="address">Level 17, Marlow Tower 7 Marlow Square Sydney, NSW 2011 Australia</p>
  </section>

  <section class="card card--back" aria-label="Business card back">
    <div class="brand">
      <div class="brand__mark"></div>
      <div class="brand__text">
        <span class="brand__name">Varentoria</span>
        <span class="brand__tagline">Assessing Executive Potential</span>
      </div>
    </div>

    <div class="divider">
      <span class="divider__rule"></span>
      <span class="divider__label web">www.<span class="web__accent">varentoria-example</span>.com.au</span>
      <span class="divider__rule divider__rule--end"></span>
    </div>
  </section>
</main>
</body>
</html>
```